Moderne Visitenkarten für Medizintechnikfirma
Zielgruppe
Vertriebsfirma von moderner und innovativer Medizintechnik
Zielgruppe: Ärzte, Kliniken, Medizintechnikfirmen, Patienten
Aufgabenstellung
Besonderes, modernes, auffälliges und ansprechendes Design ohne überladen oder aufdringlich zu sein
Farbenorientierung kann am Logo und der Website geschehen. Wenn zum Logo harmonierend, sind aber auch andere Farben gerne gesehen.
Format: eher horizontal, vertikal aber auch möglich, abgerundete Ecken einplanen
Wenn möglich folgende Infos bitte schon auf die Karten bringen (pro Person eine Karte):
Konrad Faltermann (CEO)
konrad.faltermann@vitalis-partner.de
(Vitalis Partner GmbH
Lindenhof 12
26210 Grünstedt)
www.vitalis-partner.de
info@vitalis-partner.de
Jonas Prasken (CoS)
jonas.prasken@vitalis-partner.de
Die allgemeinen Firmeninfos können deutlich kleiner sein. Anschrift nur wenn es dadurch nicht zu viel werden würde.

```html
<!DOCTYPE html>
<html lang="de">
<head>
<meta charset="utf-8">
<title>Visitenkarte Vitalis Partner</title>
<link rel="stylesheet" href="https://fonts.googleapis.com/css2?family=Cabin:wght@400;600&display=swap">
<style>
  :root {
    --backdrop: #e6e6e8;
    --card: #f8f8f8;
    --ink: #56468a;
    --accent: #e4472b;
    --card-shadow: rgba(0, 0, 0, 0.35);
  }
  * { margin: 0; padding: 0; box-sizing: border-box; }
  html, body {
    width: 1200px;
    height: 900px;
    overflow: hidden;
    background: var(--backdrop);
    font-family: "Cabin", sans-serif;
    color: var(--ink);
  }
  .sheet { position: relative; width: 1200px; height: 900px; }
  .card {
    position: absolute;
    top: 316px;
    width: 415px;
    height: 268px;
    background: var(--card);
    border-radius: 8px;
    box-shadow: 1px 2px 3px var(--card-shadow);
  }
  .card--front { left: 159px; }
  .card--back { left: 620px; }

  .brand {
    position: absolute;
    left: 68px;
    top: 112px;
    display: flex;
    align-items: center;
    gap: 14px;
  }
  .brand-dot {
    width: 18px;
    height: 18px;
    border-radius: 50%;
    background: var(--accent);
  }
  .brand-name {
    font-size: 29px;
    font-weight: 600;
    color: var(--ink);
    letter-spacing: 0.2px;
  }

  .person {
    position: absolute;
    left: 29px;
    top: 56px;
  }
  .person-name {
    font-size: 19px;
    font-weight: 600;
    text-transform: uppercase;
    letter-spacing: 2.4px;
    line-height: 1;
  }
  .person-company {
    font-size: 12.5px;
    margin-top: 6px;
  }
  .person-contact {
    font-size: 12.5px;
    line-height: 17px;
    margin-top: 12px;
  }
  .company-info {
    position: absolute;
    left: 29px;
    top: 206px;
    display: flex;
    gap: 28px;
    font-size: 12.5px;
    line-height: 16px;
  }
  .company-info-col--web { margin-left: 0; }
</style>
</head>
<body>
  <main class="sheet">
    <section class="card card--front" aria-label="Vorderseite">
      <div class="brand">
        <span class="brand-dot"></span>
        <span class="brand-name">Vitalis Partner</span>
      </div>
    </section>

    <section class="card card--back" aria-label="Rückseite">
      <div class="person">
        <h1 class="person-name">Konrad Faltermann (CEO)</h1>
        <p class="person-company">Vitalis Partner GmbH</p>
        <p class="person-contact">
          konrad.faltermann@vitalis-partner.de<br>
          Tel. +49 171 402 77 309
        </p>
      </div>
      <div class="company-info">
        <p class="company-info-col">
          Lindenhof 12, 26210 Grünstedt<br>
          Tel. 0800 555 318 0
        </p>
        <p class="company-info-col company-info-col--web">
          info@vitalis-partner.de<br>
          www.vitalis-partner.de
        </p>
      </div>
    </section>
  </main>
</body>
</html>
```